Building company buisness cards

We are looking for a sharp modern new look for our business cards.
We are a New Zealand based company that specialises in house and land packages.
We have attached a photo of the current logo and would like to see if it can be improved somehow if needed.
We are open to any colours but we have chosen green at this stage.
Feel free to change the font and make the logo smarter looking.
Play with the colours and see what looks best.

We want a card that looks so good know one will want to throw it away!

Target Market(s)

Home buyers

Industry/Entity Type

Building

Contact Information for Business Card

Derek Tolvane
0217394062
dtolvane@quillmarkhomesteads.co.nz
quillmarkhomesteads.co.nz

Font styles to use
Serif
Sans Serif

Colors

Designer to choose colors to be used in the design.

Requirements
Must have
• Logo and company name on one side, details on the other side
Nice to have
• Color codes for the original green are HEX #4a8028, RGB(74,128,40), CMYK(42,0,69,50)
• Round corners, Raised and/or spot UV

```html
<!DOCTYPE html>
<html lang="en">
<head>
<meta charset="utf-8">
<title>Quillmark Homesteads – Business Card</title>
<link href="https://fonts.googleapis.com/css2?family=Montserrat:wght@600;800&family=Roboto:wght@400;500&display=swap" rel="stylesheet">
<style>
  :root {
    --brand-green: #4a8028;
    --wave-grey: #6b6d6e;
    --ink: #444648;
    --muted: #666;
    --paper: #ffffff;
    --backdrop: #2a2d2f;
  }
  * { margin: 0; padding: 0; box-sizing: border-box; }
  html, body { width: 1200px; height: 738px; overflow: hidden; }
  body {
    background: var(--backdrop);
    position: relative;
    font-family: "Roboto", Arial, sans-serif;
  }
  .card {
    position: absolute;
    top: 214px;
    width: 540px;
    height: 309px;
    border-radius: 10px;
    overflow: hidden;
    box-shadow: 0 10px 30px rgba(0,0,0,.45);
  }
  /* Front side */
  .card--front { left: 40px; background: var(--brand-green); }
  .front-wordmark {
    position: absolute;
    left: 0; right: 0; top: 92px;
    text-align: center;
    color: var(--paper);
    font-family: "Montserrat", Arial, sans-serif;
    font-weight: 800;
    line-height: 1;
  }
  .front-wordmark .line-1 { display: block; font-size: 30px; letter-spacing: .5px; }
  .front-wordmark .line-2 { display: block; font-size: 42px; margin-top: 4px; }
  .front-web {
    position: absolute;
    left: 0; right: 0; bottom: 26px;
    text-align: center;
    color: var(--paper);
    font-size: 11px;
    font-weight: 500;
    letter-spacing: .6px;
  }
  /* Back side */
  .card--back { left: 620px; background: var(--paper); }
  .back-wordmark {
    position: absolute;
    left: 34px; top: 44px;
    color: var(--brand-green);
    font-family: "Montserrat", Arial, sans-serif;
    font-weight: 800;
    line-height: 1;
  }
  .back-wordmark .line-1 { display: block; font-size: 19px; padding-left: 26px; }
  .back-wordmark .line-2 { display: block; font-size: 25px; margin-top: 3px; }
  .person {
    position: absolute;
    right: 34px; top: 64px;
    text-align: right;
  }
  .person-name {
    font-family: "Montserrat", Arial, sans-serif;
    font-weight: 800;
    font-size: 19px;
    color: var(--brand-green);
  }
  .person-role { font-size: 9px; color: var(--muted); margin-top: 1px; }
  .divider {
    position: absolute;
    left: 34px; right: 34px; top: 118px;
    height: 1px;
    background: var(--brand-green);
  }
  .contacts {
    position: absolute;
    left: 36px; top: 140px;
    list-style: none;
    font-size: 11.5px;
    color: var(--ink);
  }
  .contacts li { display: flex; align-items: center; gap: 8px; height: 17px; }
  .contacts svg { width: 10px; height: 10px; flex: none; }
  .contacts .accent { color: var(--brand-green); }
  .wave { position: absolute; left: 0; top: 0; width: 540px; height: 309px; }
</style>
</head>
<body>

  <section class="card card--front" aria-label="Card front">
    <div class="front-wordmark">
      <span class="line-1">quillmark</span>
      <span class="line-2">homesteads.</span>
    </div>
    <p class="front-web">www.quillmarkhomesteads.co.nz</p>
  </section>

  <section class="card card--back" aria-label="Card back">
    <svg class="wave" viewBox="0 0 540 309" aria-hidden="true">
      <path d="M0,228 C140,275 270,262 365,180 C430,125 490,104 540,100 L540,309 L0,309 Z" fill="var(--wave-grey)"/>
      <path d="M0,268 C150,300 295,262 395,188 C455,143 502,124 540,121 L540,309 L0,309 Z" fill="var(--brand-green)" stroke="var(--paper)" stroke-width="5"/>
    </svg>

    <div class="back-wordmark">
      <span class="line-1">quillmark</span>
      <span class="line-2">homesteads.</span>
    </div>

    <div class="person">
      <p class="person-name">Derek Tolvane</p>
      <p class="person-role">Founder</p>
    </div>

    <div class="divider"></div>

    <ul class="contacts">
      <li>
        <svg viewBox="0 0 10 10" aria-hidden="true"><path d="M2.2 0.8 L3.8 2.8 L3 3.8 Q4 5.9 6.2 7 L7.2 6.2 L9.2 7.8 L8.2 9.2 Q4.5 9.4 2 6.5 Q0.5 4.5 0.8 1.8 Z" fill="var(--brand-green)"/></svg>
        <span>0217394062</span>
      </li>
      <li>
        <svg viewBox="0 0 10 10" aria-hidden="true"><rect x="0.8" y="2" width="8.4" height="6" fill="none" stroke="var(--brand-green)" stroke-width="1"/><path d="M0.8 2 L5 5.4 L9.2 2" fill="none" stroke="var(--brand-green)" stroke-width="1"/></svg>
        <span>dtolvane@quillmarkhomesteads.co.nz</span>
      </li>
      <li>
        <svg viewBox="0 0 10 10" aria-hidden="true"><circle cx="5" cy="5" r="4.2" fill="none" stroke="var(--brand-green)" stroke-width="1"/><ellipse cx="5" cy="5" rx="1.8" ry="4.2" fill="none" stroke="var(--brand-green)" stroke-width=".8"/><path d="M0.8 5 H9.2" stroke="var(--brand-green)" stroke-width=".8"/></svg>
        <span>www.<span class="accent">quillmarkhomesteads</span>.co.nz</span>
      </li>
    </ul>
  </section>

</body>
</html>
```